Executive recruiting firm in need of business card design

Executive recruiting firm looking for a sleek, classy and modern business card design; card itself will be square shape, rounded edges and soft touch paper, our colors are dark blues in the navy color scale, silvers and grays. Reference our website for a better idea of our company's feel and goals at Tarvex-Up.com - our company message is "Employee Engagement Begins at Recruitment" this should be on the card

```html
<!DOCTYPE html>
<html lang="en">
<head>
<meta charset="utf-8">
<title>Tarvex-Up business card</title>
<link rel="stylesheet" href="https://fonts.googleapis.com/css2?family=Questrial&family=Roboto:wght@400;500&display=swap">
<style>
  :root {
    --navy: #181a4a;
    --white: #ffffff;
    --silver: #b9bcc8;
    --stage: #e4e5e9;
    --grey-text: #7a7a86;
    --ink: #23254f;
  }
  * { margin: 0; padding: 0; box-sizing: border-box; }
  html, body {
    width: 1200px; height: 900px; overflow: hidden;
    background: var(--stage);
  }
  .stage { position: relative; width: 1200px; height: 900px; }

  .card {
    position: absolute; top: 230px;
    width: 440px; height: 440px;
    border-radius: 26px;
    box-shadow: 0 6px 18px rgba(20, 22, 50, 0.18);
    overflow: hidden;
  }
  .card--back { left: 630px; background: var(--navy); }
  .card--front { left: 130px; background: var(--white); }

  .company-name {
    font-family: "Questrial", sans-serif;
    font-weight: 400;
    letter-spacing: 5px;
    white-space: nowrap;
  }

  .card--back .company-name {
    position: absolute; left: 0; right: 0; top: 178px;
    text-align: center; font-size: 40px; color: var(--white);
  }
  .tagline {
    position: absolute; left: 0; right: 0; top: 240px;
    text-align: center;
    font-family: "Questrial", sans-serif; font-size: 14px;
    letter-spacing: 1.5px; color: var(--silver);
  }

  .card--front .company-name {
    position: absolute; right: 36px; bottom: 44px;
    font-size: 30px; color: var(--navy);
  }

  .holder { position: absolute; left: 36px; top: 40px; }
  .holder__name {
    font-family: "Questrial", sans-serif;
    font-size: 22px; color: var(--ink); font-weight: 400;
  }
  .holder__role {
    font-family: "Questrial", sans-serif;
    font-size: 15px; color: var(--grey-text); margin-top: 2px;
  }

  .contact {
    position: absolute; left: 36px; top: 140px;
    font-family: "Roboto", sans-serif; font-size: 13.5px; color: var(--ink);
    line-height: 20px; list-style: none;
  }
  .contact__address { margin-bottom: 6px; }
  .contact__row { display: flex; align-items: center; gap: 9px; }
  .contact__icon { width: 13px; height: 13px; fill: var(--grey-text); flex: none; }
</style>
</head>
<body>
<main class="stage">

  <section class="card card--front" aria-label="Card front">
    <div class="holder">
      <h1 class="holder__name">Daniel Whitford</h1>
      <p class="holder__role">Managing Director</p>
    </div>

    <ul class="contact">
      <li class="contact__address">410 East 200 South<br>Riverton City 84065</li>
      <li class="contact__row">
        <svg class="contact__icon" viewBox="0 0 16 16" aria-hidden="true"><path d="M1 5c0-2 2-3 7-3s7 1 7 3v1h-4V4.5H5V6H1z"/><path d="M3 7h10l1.5 7h-13z"/></svg>
        555.318.2047
      </li>
      <li class="contact__row">
        <svg class="contact__icon" viewBox="0 0 16 16" aria-hidden="true"><rect x="4" y="1" width="8" height="4"/><rect x="1" y="6" width="14" height="6" rx="1"/><rect x="4" y="10" width="8" height="5"/></svg>
        555.318.2051
      </li>
      <li class="contact__row">
        <svg class="contact__icon" viewBox="0 0 16 16" aria-hidden="true"><path d="M1 3h14v10H1z M2 4l6 5 6-5" stroke="#fff" stroke-width="1"/></svg>
        hello@tarvexup.com
      </li>
      <li class="contact__row">
        <svg class="contact__icon" viewBox="0 0 16 16" aria-hidden="true"><circle cx="8" cy="8" r="7"/><path d="M1 8h14M8 1c-3 4-3 10 0 14M8 1c3 4 3 10 0 14" stroke="#fff" stroke-width="1" fill="none"/></svg>
        www.tarvexup.com
      </li>
    </ul>

    <p class="company-name">TARVEX UP</p>
  </section>

  <section class="card card--back" aria-label="Card back">
    <p class="company-name">TARVEX UP</p>
    <p class="tagline">Employee Engagement Begins at Recruitment</p>
  </section>

</main>
</body>
</html>
```